Business Card Design Project

This is the first time we use our new logo. We need a business card that we can use both on our institutional corporate relationships and also that works for our staff that deals with consumers directly.

VELUNDA is a new company dedicated to empower consumers and to provide them with the best choices for specialized health care using the latest telemedicine technology (medicine at a distance via videoconference).

We want to print this cards in high quality materials and process. We will like designs that allow us to use UV spot varnish and other techniques that will differentiate us.

We are including Two different versions of Color logos. In addition we are including white over black background logos. Those can be used replacing the black for a color.

Please note this is the first time we will be creating any corporate materials with our new logo and colors.

Target Market(s)

34+ consumers of medium high and high socioeconomic levels.

Industry/Entity Type

Health

Requirements
Must have
• Our logo on its original colors
Should not have
• Any other graphical element or design that is not our logo

```html
<!DOCTYPE html>
<html lang="en">
<head>
<meta charset="utf-8">
<title>VELUNDA Business Card</title>
<link rel="stylesheet" href="https://fonts.googleapis.com/css2?family=Montserrat:wght@700&family=Arimo:wght@400&display=swap">
<style>
  :root {
    --page: #e9e9ee;
    --card-dark: #17191b;
    --card-mid: #26292c;
    --brand-blue: #1f5f8e;
    --brand-teal: #0fa39b;
    --sky: #5bb6e0;
    --text-light: #ffffff;
    --divider: #8a8d90;
  }
  html, body {
    margin: 0;
    padding: 0;
    width: 1200px;
    height: 987px;
    overflow: hidden;
    background: var(--page);
  }
  .canvas {
    position: relative;
    width: 1200px;
    height: 987px;
  }
  .card {
    position: absolute;
    left: 250px;
    width: 700px;
    height: 400px;
    border-radius: 22px;
    overflow: hidden;
    background:
      repeating-linear-gradient(90deg, rgba(255,255,255,0.025) 0 1px, transparent 1px 3px),
      linear-gradient(135deg, var(--card-mid), var(--card-dark));
    box-shadow: 0 10px 28px rgba(0,0,0,0.18);
  }
  .card-back { top: 50px; }
  .card-front { top: 520px; }

  .brand {
    position: absolute;
    display: flex;
    align-items: center;
    gap: 14px;
    font-family: "Montserrat", sans-serif;
    font-weight: 700;
    color: var(--brand-blue);
    letter-spacing: 4px;
  }
  .brand-dot {
    border-radius: 50%;
    background: var(--brand-teal);
  }
  .card-back .brand { left: 0; right: 0; top: 140px; justify-content: center; font-size: 58px; }
  .card-back .brand-dot { width: 34px; height: 34px; }
  .card-back .website {
    position: absolute;
    left: 0; right: 0; top: 250px;
    text-align: center;
    font-family: "Arimo", sans-serif;
    font-size: 22px;
    letter-spacing: 5px;
    color: var(--sky);
  }

  .card-front .brand { left: 40px; top: 110px; font-size: 44px; }
  .card-front .brand-dot { width: 26px; height: 26px; }
  .bands { position: absolute; left: 0; bottom: 0; }
  .band-website {
    position: absolute;
    right: 40px;
    bottom: 16px;
    font-family: "Arimo", sans-serif;
    font-size: 24px;
    letter-spacing: 5px;
    color: var(--text-light);
  }
  .divider {
    position: absolute;
    left: 350px;
    top: 40px;
    width: 1px;
    height: 250px;
    background: linear-gradient(var(--card-dark), var(--divider), var(--card-dark));
  }
  .contact {
    position: absolute;
    left: 385px;
    top: 42px;
    font-family: "Arimo", sans-serif;
    color: var(--sky);
  }
  .person-name {
    font-family: "Montserrat", sans-serif;
    font-weight: 700;
    font-size: 30px;
    margin: 0;
  }
  .person-title {
    font-size: 20px;
    color: var(--brand-teal);
    margin: 0 0 14px;
  }
  .contact-line {
    display: flex;
    align-items: center;
    gap: 8px;
    font-size: 19px;
    margin: 4px 0;
  }
  .contact-line svg { width: 16px; height: 16px; flex: none; }
  .address { font-size: 19px; margin-top: 12px; line-height: 1.25; }
</style>
</head>
<body>
<main class="canvas">
  <section class="card card-back" aria-label="Card back">
    <div class="brand"><span class="brand-dot"></span>VELUNDA</div>
    <div class="website">www.velunda.com</div>
  </section>

  <section class="card card-front" aria-label="Card front">
    <div class="brand"><span class="brand-dot"></span>VELUNDA</div>

    <svg class="bands" width="700" height="150" viewBox="0 0 700 150" aria-hidden="true">
      <polygon points="0,30 300,30 320,60 320,70 0,70" fill="var(--brand-teal)"/>
      <polygon points="0,80 320,80 335,90 700,90 700,150 0,150" fill="var(--sky)"/>
    </svg>
    <div class="band-website">www.velunda.com</div>

    <div class="divider"></div>

    <div class="contact">
      <p class="person-name">Your Name</p>
      <p class="person-title">Title</p>
      <div class="contact-line">
        <svg viewBox="0 0 16 16"><circle cx="8" cy="8" r="7.5" fill="var(--sky)"/><path d="M5 4.5l2 2-1 1c.6 1.2 1.4 2 2.5 2.5l1-1 2 2-1.2 1.2C7.5 12 4 8.5 3.8 5.7z" fill="var(--card-dark)"/></svg>
        012-345-6789
      </div>
      <div class="contact-line">
        <svg viewBox="0 0 16 16"><circle cx="8" cy="8" r="7.5" fill="var(--sky)"/><path d="M5 4.5l2 2-1 1c.6 1.2 1.4 2 2.5 2.5l1-1 2 2-1.2 1.2C7.5 12 4 8.5 3.8 5.7z" fill="var(--card-dark)"/></svg>
        012-345-6789
      </div>
      <div class="contact-line">
        <svg viewBox="0 0 16 16"><rect x="1" y="3" width="14" height="10" rx="1.5" fill="var(--sky)"/><path d="M1.5 4l6.5 5 6.5-5" stroke="var(--card-dark)" stroke-width="1.4" fill="none"/></svg>
        name@velunda.com
      </div>
      <div class="address">Street Name, City Name<br>State, City Zip Code</div>
    </div>
  </section>
</main>
</body>
</html>
```